Home Loan Introducer needs logo/business cards

We need a simple but classy logo for business cards and flyers. The business is a home loan referral business that is called an Introducer. The business name is "The Harborline".
I was thinking very simple and straight to the point on the front with "Home Loans" the only thing on the front with a nice background colour/s.
Then on the back, "The Harborline"
and "Quality Customer Service"
and "Email, text or call welcome"
and then my name, email address and phone number.
Updates
Thank you for all the designs :-)
Target Market(s)
Home buyers.
Home owners.
Investors.
Industry/Entity Type
Loan
Look and feel

```html
<!DOCTYPE html>
<html lang="en">
<head>
<meta charset="utf-8">
<title>The Harborline – Business Cards</title>
<link rel="stylesheet" href="https://fonts.googleapis.com/css2?family=Ubuntu:wght@400;500;700&display=swap">
<style>
  :root {
    --backdrop: #ddd8d1;
    --card-dark: #1f1f1f;
    --card-yellow: #fdb03a;
    --brand-blue: #1a6fc4;
    --text-light: #ffffff;
    --text-dark: #1c1c1c;
    --house-shade: #2a2a2a;
  }
  * { margin: 0; padding: 0; box-sizing: border-box; }
  html, body {
    width: 1200px; height: 750px; overflow: hidden;
    background: var(--backdrop);
    font-family: "Ubuntu", sans-serif;
  }
  .canvas { position: relative; width: 1200px; height: 750px; }

  .card {
    position: absolute;
    box-shadow: 0 10px 24px rgba(0,0,0,0.28);
    overflow: hidden;
  }

  /* Contact side */
  .card--contact {
    left: 90px; top: 110px; width: 500px; height: 300px;
    background: var(--card-dark);
  }
  .contact__top {
    height: 180px;
    display: flex; flex-direction: column; align-items: center;
    padding-top: 42px;
  }
  .brand {
    display: flex; align-items: center; gap: 12px;
  }
  .brand__dot {
    width: 26px; height: 26px; border-radius: 50%;
    background: var(--brand-blue);
  }
  .brand__name {
    font-weight: 700; font-size: 26px; letter-spacing: 0.5px;
    color: var(--card-yellow); text-transform: uppercase;
  }
  .features {
    list-style: none; margin-top: 22px;
    font-size: 14px; color: var(--brand-blue);
  }
  .features li { display: flex; align-items: center; gap: 6px; line-height: 20px; }
  .features svg { width: 13px; height: 13px; }

  .contact__bottom {
    height: 120px; background: var(--card-yellow);
    display: flex; flex-direction: column; align-items: center;
    padding-top: 16px;
  }
  .person__name { font-size: 19px; font-weight: 500; color: var(--text-dark); }
  .person__rule { width: 160px; height: 2px; background: var(--text-light); margin: 4px 0 6px; }
  .person__detail { font-size: 9.5px; color: var(--text-light); line-height: 13px; }
  .person__detail span { color: var(--brand-blue); }

  /* Front side */
  .card--front {
    left: 610px; top: 300px; width: 540px; height: 330px;
    background: var(--card-dark);
  }
  .front__houses {
    position: absolute; left: 110px; top: 40px; width: 320px; height: 130px;
    background: radial-gradient(ellipse at 50% 70%, var(--house-shade) 0%, rgba(42,42,42,0) 70%);
  }
  .front__band {
    position: absolute; left: 28px; top: 164px; width: 484px; height: 80px;
    background: var(--card-yellow); border-radius: 7px;
    display: flex; align-items: center; justify-content: center;
  }
  .front__title {
    font-weight: 700; font-size: 52px; letter-spacing: 1px;
    color: var(--text-light); text-transform: uppercase;
  }
</style>
</head>
<body>
<main class="canvas">

  <section class="card card--contact">
    <div class="contact__top">
      <div class="brand">
        <span class="brand__dot"></span>
        <span class="brand__name">The Harborline</span>
      </div>
      <ul class="features">
        <li><svg viewBox="0 0 12 12"><path d="M1 6.5 L4.5 10 L11 1.5" fill="none" stroke="#fff" stroke-width="2"/></svg>Quality Customer Service</li>
        <li><svg viewBox="0 0 12 12"><path d="M1 6.5 L4.5 10 L11 1.5" fill="none" stroke="#fff" stroke-width="2"/></svg>Email, text or call welcome</li>
      </ul>
    </div>
    <div class="contact__bottom">
      <p class="person__name">Owen Hale</p>
      <div class="person__rule"></div>
      <p class="person__detail">Phone: <span>+6391847265</span></p>
      <p class="person__detail">Email: <span>owen@harborline.net</span></p>
    </div>
  </section>

  <section class="card card--front">
    <div class="front__houses" role="img" aria-label="Faint row of house silhouettes"></div>
    <div class="front__band">
      <h1 class="front__title">Home Loan</h1>
    </div>
  </section>

</main>
</body>
</html>
```